New, modern business card for growing audiology practice

We need a new business card for our audiology practice. Our logo and website have recently changed (more modern) and we want our business cards to reflect this change.
We conduct hearing tests, perform earwax removals, and fit & dispense hearing aids to our patients. We are a family owned practice in which the owner is the one who works directly with the patient. I have attached logos in various formats to use, as well as two ideas I found on this website; as well as a scanned copy of our current logo. Good luck!

Industry/Entity Type

Business

Contact Information for Business Card

Company name: Tolvera Hearing Center
Provider name: Peter Wolstenby, Au.D. F/NSB
Phone number: (440) 683-5127
Address: 837 W. Lindell Ave. Harlow Brook, OH 44187
email: tolverahearing@postvane.com
website: tolverahearing.com

Colors
000000
aaaaaa
dbdbdb
cacaca
9bcb3c
afd23c
cadf82
b1b1b1

Requirements
Must have
• My card must include information in the "details" section. In the attached images, I found a few that I liked and I would like to model after - "brisky bouncin'" and "Sound Method Center".
• Must be horizontal.
• Must include logos provided. I uploaded them in various file formats and various ways.
• Must match logo font, if possible, if not, please get as close as you can.
Nice to have
• I really like the idea of having a color on one side with just the logo and company name and the contact information and provider name on the other side. I also really like the idea of having the main color dominating on the logo/company side with accent of that same color on the contact side of the card.
Should not have
• Must not be vertical.

```html
<!DOCTYPE html>
<html lang="en">
<head>
<meta charset="utf-8">
<title>Tolvera Hearing Center – Business Card</title>
<link rel="stylesheet" href="https://fonts.googleapis.com/css2?family=Lato:wght@400&family=Roboto:wght@400&family=Roboto+Condensed:wght@400;700&display=swap">
<style>
  :root {
    --backdrop: #d6b08a;
    --card: #f7f7f6;
    --green: #6a9a34;
    --black: #000000;
    --ink: #111111;
    --grey-text: #555555;
    --url-grey: #444444;
    --white: #ffffff;
  }
  html, body {
    margin: 0;
    padding: 0;
    width: 1200px;
    height: 960px;
    overflow: hidden;
    background: var(--backdrop);
  }
  .canvas {
    position: relative;
    width: 1200px;
    height: 960px;
  }
  .card {
    position: absolute;
    left: 320px;
    width: 600px;
    background: var(--card);
    border-radius: 18px;
    overflow: hidden;
  }
  .card--front { top: 100px; height: 350px; }
  .card--back  { top: 493px; height: 342px; }

  .brand {
    position: absolute;
    left: 0;
    right: 0;
    top: 162px;
    text-align: center;
  }
  .brand__name {
    margin: 0;
    font-family: "Lato", sans-serif;
    font-weight: 400;
    font-size: 31px;
    letter-spacing: 0.5px;
    color: var(--ink);
    line-height: 1;
  }
  .brand__url {
    margin: 12px 0 0;
    font-family: "Roboto", sans-serif;
    font-size: 13px;
    letter-spacing: 6.2px;
    color: var(--url-grey);
  }

  .swoosh {
    position: absolute;
    left: 0;
    top: 0;
    width: 600px;
    height: 342px;
  }
  .swoosh__band  { fill: var(--green); }
  .swoosh__edge  { fill: var(--black); }
  .swoosh__light { fill: var(--white); }

  .provider {
    position: absolute;
    left: 35px;
    top: 26px;
    font-family: "Roboto Condensed", sans-serif;
    color: var(--white);
  }
  .provider__name {
    margin: 0;
    font-weight: 700;
    font-size: 21px;
    line-height: 1.1;
  }
  .provider__title {
    margin: 4px 0 0;
    font-weight: 400;
    font-size: 16px;
    letter-spacing: 0.3px;
  }

  .contact {
    position: absolute;
    left: 35px;
    top: 208px;
    font-family: "Roboto", sans-serif;
    font-size: 14px;
    color: var(--grey-text);
    line-height: 19px;
  }
  .contact__address { margin: 0 0 9px; }
  .contact__list { list-style: none; margin: 0; padding: 0; }
  .contact__item { display: flex; align-items: center; gap: 7px; }
  .contact__icon { width: 14px; height: 14px; fill: var(--green); flex: none; }
</style>
</head>
<body>
<main class="canvas">

  <section class="card card--front" aria-label="Card front">
    <div class="brand">
      <p class="brand__name">TOLVERA HEARING CENTER</p>
      <p class="brand__url">www.tolverahearing.com</p>
    </div>
  </section>

  <section class="card card--back" aria-label="Card back">
    <svg class="swoosh" viewBox="0 0 600 342" aria-hidden="true">
      <path class="swoosh__edge" d="M0 70 C4 96 18 118 50 128 C95 138 170 124 250 96 C160 114 85 120 48 112 C22 106 8 92 0 74 Z"/>
      <path class="swoosh__band" d="M0 0 H600 V62 C520 42 390 66 250 96 C160 114 85 118 46 110 C20 104 6 90 0 74 Z"/>
      <path class="swoosh__light" d="M350 50 C430 22 520 22 562 56 C512 36 440 36 350 50 Z"/>
    </svg>

    <div class="provider">
      <p class="provider__name">PETER WOLSTENBY</p>
      <p class="provider__title">AU.D. F/NSB</p>
    </div>

    <div class="contact">
      <p class="contact__address">837 W. Lindell Ave.<br>Harlow Brook, OH 44187</p>
      <ul class="contact__list">
        <li class="contact__item">
          <svg class="contact__icon" viewBox="0 0 16 16" aria-hidden="true"><path d="M3.5 1 L6 1 L7 5 L5.2 6.3 C6 8 7.8 9.9 9.7 10.8 L11 9 L15 10 L15 12.5 C15 14 14 15 12.5 15 C6.5 15 1 9.5 1 3.5 C1 2 2 1 3.5 1 Z"/></svg>
          <span>(440) 683-5127</span>
        </li>
        <li class="contact__item">
          <svg class="contact__icon" viewBox="0 0 16 16" aria-hidden="true"><path d="M1 3.5 H15 V4.5 L8 9 L1 4.5 Z M1 6 L8 10.5 L15 6 V13 H1 Z"/></svg>
          <span>tolverahearing@postvane.com</span>
        </li>
        <li class="contact__item">
          <svg class="contact__icon" viewBox="0 0 16 16" aria-hidden="true"><circle cx="8" cy="8" r="7"/><path d="M8 1 V15 M1 8 H15" stroke="#f7f7f6" stroke-width="1.2" fill="none"/></svg>
          <span>tolverahearing.com</span>
        </li>
      </ul>
    </div>
  </section>

</main>
</body>
</html>
```